New web/graphic designs required to improve existing ecommerce site.

Initial outline of project:
This project is for new designs to fit into areas of existing webpages - specifically:-
Objective 1 - Produce 8 home page design proposals (design for central area of page only, not whole page)
Objective 2 - Produce 5 designs for page header banners (950px x 84px images)
Objective 3 - Produce 10 designs for help guide covers (316px x 410px images)
Also, on a more general note:
Objective 4 - Review and suggest improvements for other areas website. (This may lead to further design work)
-
Introduction to the Periodical Bazaar website:
The Periodical Bazaar website is a marketplace where back-issue hobby magazines can be bought and sold, and in some cases downloaded & viewed in digital form. The ‘sellers’ of the magazines will be both traders and private individuals. Trade sellers will also be able to sell magazine subscriptions and have ‘Promotion Pages’ about themselves and/or their magazine titles on the site. Other forms of advertising will also be available on the site for any commercial advertisers who want it, particularly for companies supplying the various hobbies covered.
Users of the website can locate magazines of interest to them by browsing through the hobby / category sections of the site, or by doing keyword searches for issues containing articles on specific topics.
The site is split-up into sections dealing with magazines about specific hobby subjects – ie., cars, motorbikes, railway, aviation, boating etc. Although part of the larger site, each of these sections is largely self-contained, with many users only ever browsing in the section related to their hobby. As such, each section effectively has it’s own home page, which will duplicate much of the information shown on the main home page. These multiple ‘section home pages’ will be promoted in their own right via URLs specific to that hobby. Currently there are 8 sections, but this number is expected to increase as the site grows.
This website is still being developed, but is close to launch; as such the website is fully functional but a lot of content is missing - please bear this in mind when viewing the site, and feel free to ask for clarification if anything is unclear.
The new website is currently at: http://www2.periodicalbazaar.co.uk
This website will replace several existing sites:-
http://www.periodicalbazaar.co.uk
http://www.twowheel-journals.co.uk
http://www.skyward-journals.co.uk
http://www.drivepapers.co.uk
http://www.trackside-journals.co.uk
http://www.scalecraft-journals.co.uk
-
Design notes:
The overall design is fairly conventional and very much ‘functionality’ driven, the website being at it’s heart an ecommerce system with some fairly complex features. Nevertheless I want the site to appear simple and modern in appearance, being somewhere between an ‘all style’ Web 2.0-type site (eg. tintly.io), and an ‘all function’ conventional trading site (eg. Bravlo, Quibb etc). A good example of a style of site which I would like to emulate is PostGecko – a complex and large site made to look friendly and approachable by the use of simple, clear design, bold colour and a sense of humour.
To explain further what is required I have prepared various image documents which include more detailed notes on the various objectives for this project. There is a lot of information in these documents - please read them carefully:-
Objective 1:
- Produce 1 'Main Home Page' design proposal
- Produce 8 'Section Home Page' design proposals - one each for these sections: Railway, Boating, Aviation, Cycling, Automotive, Motorcycling, Men's Lifestyle, Modelling
More information on Objective 1 is given in these image documents:
http://www.filenook.net/Home_Page_Designs-Purpose.gif
http://www.filenook.net/Home_Page_Designs-Areas.gif
http://www.filenook.net/Section_Home_Pages-1.gif
http://www.filenook.net/Section_Home_Pages-2.gif
-
Objective 2:
- Produce 5 designs for page header banners (950px x 84px images)
More information on Objective 2 is given in this image document:
http://www.filenook.net/Page_Header_Banners.gif
-
Objective 3:
- Produce 10 designs for help guide covers (316px x 410px images)
http://www.filenook.net/Help_Guide_Covers.gif
-
Objective 4:
- Review and suggest improvements for other areas website
I would like the designer to spend some time looking at the whole of the current website, and suggest any areas that can be improved. I am not looking for a wholesale re-design - the overall layout of the site and major design elements such as the navigation system - are essentially fixed - however, many graphical elements can be changed, as can any text content (including text content within the navigation system).
Improvements which are suggested may lead to additional design work either as part of this project, or as subsequent projects in their own right.
-
Designers are very welcome to contact me to discuss any aspect of this project, or if more information is required about the website or the designs required.
I'm happy to guarantee this project in due course, if there is positive reaction to the project from potential designers interested in submitting designs. This is the second project I have run on ArtBrigade - the first one was successful and resulted in the Flash animation that is currently on the homepage of the website.
UPDATE 11/10/11:
I've created some new documents to illustrate the sort of designs I am looking for for the Main Home Page and Section Home Pages:
Very rough examples of the sort of style I am looking for:
http://www.filenook.net/Rough_Main_Home_Page_1.jpg
http://www.filenook.net/Rough_Main_Home_Page_2.jpg
http://www.filenook.net/Rough_Main_Home_Page_3.jpg
http://www.filenook.net/Rough_Main_Home_Page_4.jpg
http://www.filenook.net/Rough_Main_Home_Page_5.jpg
http://www.filenook.net/Rough_Section_Home_Page.jpg
http://www.filenook.net/Rough_Section_Home_Page_2.jpg
Detailed document showing exact content required for the Main Home Page and each Section Home Page:
http://www.filenook.net/Home_Page_Content.gif
Target Market(s)
Mainly male, age 20 - 60. Not necessarily 'web savvy' or design-conscious
Industry/Entity Type
Advertising
Look and feel

```html
<!DOCTYPE html>
<html lang="en">
<head>
<meta charset="utf-8">
<title>Periodical Bazaar – Home</title>
<link href="https://fonts.googleapis.com/css2?family=Arimo:wght@400;700&family=Lilita+One&display=swap" rel="stylesheet">
<style>
:root{
  --backdrop:#2a2a2a;
  --page:#c4c4c4;
  --ink:#222;
  --black:#0d0d0d;
  --yellow:#f6c400;
  --yellow-deep:#e2a200;
  --brand-red:#c0141c;
  --heading-red:#a3121a;
  --green:#3aa318;
  --green-deep:#23780c;
  --olive:#6e5a12;
  --olive-deep:#3f300a;
  --blue-tri:#2a9fd0;
  --rule:#8f8f8f;
  --white:#fff;
  --footer-link:#f2f2f2;
}
*{box-sizing:border-box;margin:0;padding:0}
html,body{width:1200px;height:900px;overflow:hidden;background:var(--backdrop);font-family:"Arimo",Arial,sans-serif;color:var(--ink)}
.canvas{position:relative;width:1200px;height:900px;overflow:hidden}
.page{position:absolute;left:308px;top:0;width:604px;height:900px;background:var(--page)}
.abs{position:absolute}

/* header */
.masthead{left:316px;top:0;width:594px;height:42px;background:linear-gradient(#ffe055,var(--yellow) 45%,var(--yellow-deep));border:2px solid #3a2d00;border-top:none;border-radius:0 0 12px 12px}
.wordmark{left:332px;top:8px;font-size:19px;font-weight:700;color:var(--brand-red);letter-spacing:-.3px}
.phone{left:802px;top:6px;width:80px;height:11px;background:#e9e9e9;border:1px solid #999;font-size:8px;line-height:9px;text-align:right;padding-right:3px;color:#333}
.phone-icon{left:886px;top:4px}
.search-label{left:739px;top:21px;font-size:9px;font-weight:700;color:#111}
.search-input{left:775px;top:20px;width:106px;height:13px;background:#fff;border:1px solid #777}
.search-go{left:884px;top:20px;width:19px;height:13px;background:var(--black);color:#fff;font-size:8px;text-align:center;line-height:13px}
.tabs{left:323px;top:42px;display:flex;gap:3px}
.tab{height:16px;background:var(--black);color:#fff;font-size:9px;font-weight:700;text-align:center;line-height:15px;border-radius:0 0 6px 6px;white-space:nowrap}
.userlinks{left:686px;top:47px;font-size:9px;color:#fff;word-spacing:1px;white-space:nowrap}
.userlinks b{color:#e8e8e8;font-weight:700}

/* hero */
.hero{left:314px;top:64px;width:594px;height:114px;background:linear-gradient(180deg,#b9e2f6 0%,#e3f4fb 45%,#7dc24a 75%,#4c8d2b 100%)}
.hero-art{left:470px;top:64px;width:330px;height:114px;background:radial-gradient(ellipse at 50% 80%,#6fb83c 0%,#8fcf5a 40%,rgba(140,200,230,0) 75%)}
.hero-left{left:322px;top:70px;font-size:21px;line-height:20px;color:#1b5fa8}
.hero-left span{display:block;font-size:32px;line-height:30px;padding-left:36px}
.hero-right{left:740px;top:70px;text-align:right;width:162px;font-size:19px;line-height:20px;color:#1a2a3a}
.hero-right span{display:block;font-size:30px;line-height:32px}

/* sidebar */
.bar-title{background:var(--black);color:#fff;font-size:10px;font-weight:700;line-height:21px;border-radius:4px}
.browse{left:314px;top:183px;width:148px;height:21px;padding-left:14px;white-space:nowrap}
.sections{left:318px;top:208px;width:141px;list-style:none}
.sections li{height:20.6px;border-bottom:1px solid var(--rule);font-size:9px;font-weight:700;line-height:20px;padding-left:23px;position:relative;color:#1a1a1a}
.sections li::before{content:"";position:absolute;left:2px;top:6px;border-left:8px solid var(--blue-tri);border-top:4px solid transparent;border-bottom:4px solid transparent}
.jump{left:319px;top:377px;width:140px;height:21px;background:var(--black);border-radius:3px}
.jump-select{left:326px;top:381px;width:126px;height:13px;background:#fff;border:1px solid #777;font-size:8px;line-height:11px;padding-left:5px;white-space:nowrap}
.jump-arrow{left:440px;top:382px;width:11px;height:11px;background:#ddd;border-left:1px solid #888}
.adslot{left:320px;top:408px;width:138px;height:245px}
.adslot-label{left:320px;top:522px;width:138px;text-align:center;font-size:15px;font-weight:700;color:#111}

/* article search */
.article-search{left:472px;top:183px;width:438px;height:22px}
.as-label{left:497px;top:189px;font-size:9px;font-weight:700;color:#fff}
.as-input{left:600px;top:187px;width:95px;height:13px;background:#fff;border:1px solid #777;font-size:8px;line-height:11px;padding-left:3px;color:#555}
.as-select{left:713px;top:187px;width:93px;height:13px;background:#fff;border:1px solid #777;font-size:8px;line-height:11px;padding-left:3px;color:#333}
.as-button{left:828px;top:187px;width:62px;height:13px;background:linear-gradient(#ffe15a,var(--yellow-deep));border-radius:3px;font-size:9px;line-height:13px;text-align:center;color:#222}
.crumb{left:484px;top:209px;font-size:9px;font-weight:700;color:#fff}

/* welcome */
.welcome{left:475px;top:222px;width:433px;height:126px;background:linear-gradient(180deg,#a38418 0%,var(--olive) 40%,var(--olive-deep) 100%);border:2px solid var(--yellow-deep);border-radius:7px}
.welcome-title{left:486px;top:228px;font-family:"Lilita One","Arimo",sans-serif;font-size:22px;color:var(--yellow);letter-spacing:.3px;white-space:nowrap}
.welcome-sub{left:487px;top:252px;font-size:11px;font-weight:700;color:#fff}
.cta{border-radius:8px;color:#fff;text-align:center;font-size:13px;letter-spacing:.5px;white-space:nowrap}
.cta b{font-weight:700;font-size:13px}
.cta-search{left:483px;top:273px;width:182px;height:33px;background:linear-gradient(#e43038,#8e0c12);padding-top:3px;line-height:12px;color:#fff}
.cta-search small{display:block;font-size:8px;letter-spacing:0;font-weight:700;line-height:11px}
.cta-read,.cta-sell,.cta-buy{height:30px;line-height:30px;background:linear-gradient(#5fcf2a,var(--green) 55%,var(--green-deep))}
.cta-read{left:483px;top:311px;width:182px}
.cta-sell{left:718px;top:276px;width:182px;color:#111}
.cta-buy{left:718px;top:312px;width:182px;color:#111}
.mascot{left:668px;top:258px;width:50px;height:86px;border-radius:20px 20px 6px 6px;background:linear-gradient(#c9d7e6,#5a80b4)}

/* content */
.content{left:475px;top:356px;width:433px;height:297px;background:#fff;border-radius:7px}
.col-left{left:490px;top:372px;width:186px}
.col-left h2,.col-right h2{font-size:10px;font-weight:700;color:var(--heading-red);margin-bottom:5px;white-space:nowrap}
.col-left p{font-size:7.4px;line-height:8.4px;color:#333;margin-bottom:9px}
.divider{left:681px;top:366px;width:1px;height:276px;background:#bbb}
.sellbox{left:686px;top:363px;width:212px;height:152px;background:linear-gradient(#6a6a6a,#3a3a3a);border:2px solid #b0141a;border-radius:6px}
.sellbox-title{left:694px;top:370px;font-size:14px;font-weight:700;font-style:italic;color:#fff;white-space:nowrap}
.sellbox-sub{left:740px;top:387px;font-size:11px;font-weight:700;font-style:italic;color:#e51d25}
.sellbox-art{left:694px;top:410px;width:94px;height:76px;border-radius:8px;background:radial-gradient(circle at 50% 55%,#8fa9c9,#4d5d73 70%,rgba(0,0,0,0) 72%)}
.sellbox-list{left:794px;top:404px;font-size:6.6px;line-height:8.8px;color:#fff}
.sellbox-list b{color:var(--yellow);font-style:italic;font-size:7px;display:block}
.sellbox-list span{display:block;padding-left:8px}
.learn{left:746px;top:486px;width:106px;height:20px;background:linear-gradient(#e63038,#900d12);border:1px solid #fff;border-radius:4px;color:#fff;font-size:9px;font-weight:700;font-style:italic;text-align:center;line-height:18px}
.col-right{left:690px;top:522px;width:208px}
.col-right p{font-size:7.4px;line-height:8.4px;color:#333;margin-bottom:14px;margin-top:12px}

/* footer */
.rule{height:1px;background:#9c9c9c}
.foot-mark{left:308px;top:669px;width:604px;text-align:center;font-size:14px;font-weight:700;color:var(--brand-red)}
.foot-col{top:710px;font-size:9px;line-height:13px;white-space:nowrap}
.foot-col h3{font-size:9px;font-weight:400;color:#111;margin-bottom:1px}
.foot-col a{display:block;color:var(--footer-link);text-decoration:none}
.badges{left:318px;top:800px;display:flex;gap:2px}
.badge{height:26px;border-radius:13px 4px 4px 13px;background:linear-gradient(#ffe56a,var(--yellow-deep));font-size:8px;font-weight:400;line-height:26px;padding-left:5px;padding-right:20px;color:#222;position:relative;white-space:nowrap}
.badge i{position:absolute;right:2px;top:5px;width:16px;height:16px;border-radius:50%;background:#555}
.address{left:319px;top:841px;width:587px;height:21px;background:var(--black);color:#fff;font-size:9.5px;line-height:21px;padding-left:15px;word-spacing:1px;white-space:nowrap}
.address span{position:absolute;left:399px}
.copyright{left:308px;top:877px;width:604px;text-align:center;font-size:7.4px;line-height:9px;color:#fff}
</style>
</head>
<body>
<div class="canvas">
  <div class="page"></div>

  <header>
    <div class="abs masthead"></div>
    <div class="abs wordmark">periodicalbazaar.co.uk</div>
    <div class="abs phone">01632 960418</div>
    <svg class="abs phone-icon" width="14" height="12" viewBox="0 0 14 12" aria-hidden="true"><path d="M1 4c0-3 12-3 12 0l-2 1-1-1H4L3 5z M3 6h8l1 5H2z" fill="#111"/></svg>
    <div class="abs search-label">Search:</div>
    <div class="abs search-input"></div>
    <div class="abs search-go">Go</div>
    <nav class="abs tabs">
      <div class="tab" style="width:57px">Buy</div>
      <div class="tab" style="width:55px">Sell</div>
      <div class="tab" style="width:57px">My Mags</div>
      <div class="tab" style="width:53px">Help</div>
      <div class="tab" style="width:74px">All Magazines</div>
    </nav>
    <div class="abs userlinks"><b>Hello Guest</b> &nbsp;| &nbsp;Login &nbsp;| &nbsp;My basket(0) &nbsp;| &nbsp;Checkout</div>
  </header>

  <div class="abs hero" role="img" aria-label="Cartoon hobby landscape with a friendly mascot holding a magazine, a quad bike, a lake, planes and fishing"></div>
  <div class="abs hero-art" aria-hidden="true"></div>
  <div class="abs hero-left">Have a<span>hobby?</span></div>
  <div class="abs hero-right">We have the<span>magazine!</span></div>

  <aside>
    <div class="abs bar-title browse">BROWSE MAIN SECTIONS:</div>
    <ul class="abs sections">
      <li>Aviation</li><li>Automotive</li><li>Railway</li><li>Cycling</li>
      <li>Boating</li><li>Modelling</li><li>Men's lifestyle</li><li>Motorcycling</li>
    </ul>
    <div class="abs jump"></div>
    <div class="abs jump-select">Jump to a different Section</div>
    <svg class="abs jump-arrow" viewBox="0 0 11 11" aria-hidden="true"><path d="M3 4h5L5.5 7z" fill="#333"/></svg>
    <svg class="abs adslot" viewBox="0 0 138 245" aria-hidden="true">
      <rect x="1" y="1" width="136" height="243" fill="#e2e2e2" stroke="#6a6a6a" stroke-width="2"/>
      <path d="M3 3L60 100M135 3L78 100M3 242L60 145M135 242L78 145" stroke="#6a6a6a" stroke-width="2"/>
    </svg>
    <div class="abs adslot-label">BANNER</div>
  </aside>

  <div class="abs bar-title article-search"></div>
  <div class="abs as-label">ARTICLE SEARCH:</div>
  <div class="abs as-input">Keywords....</div>
  <div class="abs as-select">All Sections</div>
  <div class="abs as-button">search</div>
  <div class="abs crumb">Home</div>

  <section>
    <div class="abs welcome"></div>
    <div class="abs welcome-title">Welcome to Periodical Bazaar</div>
    <div class="abs welcome-sub">Using this website you can...</div>
    <div class="abs cta cta-search"><b>SEARCH</b> for articles<small>its like a search engine but for magazines!</small></div>
    <div class="abs cta cta-read"><b>READ</b> issues online</div>
    <div class="abs cta cta-sell"><b>SELL</b> your magazines</div>
    <div class="abs cta cta-buy"><b>BUY</b> back issues</div>
    <div class="abs mascot" role="img" aria-label="Cartoon mascot in cap and overalls"></div>
  </section>

  <main>
    <div class="abs content"></div>
    <div class="abs col-left">
      <h2>Back Issue Hobby Magazines</h2>
      <p>Periodical Bazaar sells back-issue magazines covering hobby subjects including Automotive, Aviation, Railway, Modelling, Motorbiking, Boating, Cycling and Men's Lifestyle. Each section on our website contains dozens of magazine titles from different publishers. Use the left menu to start browsing our site...or alternatively use the...</p>
      <h2>Magazine Article Search Facility</h2>
      <p>Use the Search facility (in the horizontal black bar above) to find magazine issues containing articles on specific topics. To improve relevance you can filter your search by Section (if searching from this page), or by Category or Title (if searching from within a Section)</p>
      <h2>About Us – Buy Old Magazines Online</h2>
      <p>Periodical Bazaar is UK-based, and is an independent company offering magazines from many different publishers. At the heart of our service is a unique database of magazine issues &amp; articles covering thousands of titles stretching back to the 1950s. As well as listing our own large stocks, this website allows other private &amp; trade sellers to offer their old magazines for sale. Magazine back issues – and in some cases current issues &amp; subscriptions too – may be ordered from this site for mail-order delivery around the world</p>
    </div>
    <div class="abs divider"></div>

    <div class="abs sellbox"></div>
    <div class="abs sellbox-title">SELL YOUR MAGAZINES</div>
    <div class="abs sellbox-sub">on this website!</div>
    <div class="abs sellbox-art" role="img" aria-label="Two cartoon sellers with a stack of magazines"></div>
    <div class="abs sellbox-list">
      <b>PRIVATE SELLERS..SELL:</b><span>BACK ISSUES</span>
      <b style="margin-top:8px">TRADE SELLERS..SELL:</b><span>BACK ISSUES</span><span>CURRENT ISSUES</span><span>DIGITAL ISSUES</span><span>SUBSCRIPTIONS</span>
    </div>
    <div class="abs learn">LEARN MORE</div>

    <div class="abs col-right">
      <h2>Sell Your Magazines</h2>
      <p>Use this website to sell your old magazine collection for cash - click the button in the yellow box above for more information</p>
      <h2>Magazine Subscriptions &amp; Digital Issues</h2>
      <p>Subscriptions for many magazine titles may be purchased through this website, for yourself or as an ideal gift. In some cases individual magazine issues may also be downloaded in digital form.</p>
    </div>
  </main>

  <footer>
    <div class="abs rule" style="left:320px;top:660px;width:588px"></div>
    <div class="abs foot-mark">periodicalbazaar.co.uk</div>
    <div class="abs foot-col" style="left:347px"><h3>ABOUT US</h3><a>Who We Are</a><a>Our Service</a><a>Careers</a><a>Contact us</a></div>
    <div class="abs foot-col" style="left:469px"><h3>BUYING MAGAZINES</h3><a>Buying Back Issues</a><a>Buying Subscriptions</a><a>Buying FAQ's</a></div>
    <div class="abs foot-col" style="left:621px"><h3>SELLING MAGAZINES</h3><a>New Seller Overview</a><a>Seller Terms &amp; Conditions</a><a>Publisher Services</a><a>Register / Log-In</a></div>
    <div class="abs foot-col" style="left:783px"><h3>ADVERTISING</h3><a>Advertising Overview</a><a>Rate Card</a><a>Make Booking</a></div>
    <div class="abs rule" style="left:318px;top:783px;width:588px"></div>

    <div class="abs badges">
      <div class="badge" style="width:72px">automotive<i></i></div>
      <div class="badge" style="width:68px">modelling<i></i></div>
      <div class="badge" style="width:66px">boating<i></i></div>
      <div class="badge" style="width:68px">aviation<i></i></div>
      <div class="badge" style="width:66px">railway<i></i></div>
      <div class="badge" style="width:86px">men's lifestyle<i></i></div>
      <div class="badge" style="width:80px">motorcycling<i></i></div>
      <div class="badge" style="width:66px">cycling<i></i></div>
    </div>

    <div class="abs address">Periodical Bazaar, 12 Fenwick Row, Alderholt, Westshire, AB12 3CD, UK.<span>Email: Orders@periodicalbazaar.co.uk</span></div>
    <div class="abs copyright">Copyright © 2004-2011 Periodical Bazaar. All Rights Reserved. Designated trademarks and brands are the property of their respective owners.<br>Use of this website constitutes acceptance of the Periodical Bazaar Terms &amp; Conditions, User Agreement and Privacy Policy</div>
  </footer>
</div>
</body>
</html>
```